Corporate Branded Documents - IT Provider - On-going work

Hi, I'm Ned a Director of Harbourlane ICT Support a UK Based IT & Telecoms support firm. We've been trading for 12 years now and feel its time for a lick of paint. We have a logo, website etc but would like someone to create some standard documents for us.

- A PDF Proposal Template - We currently don't send our customers proposals as we have nothing that looks good.
- A Quote Template PDF - Example Attached
- A Order Template PDF - Example Attached
- A Invoice Template PDF - Example Attached
- A Generic Document PDF - Something we can use for customer application forms, NDA Agreements, Terms & Conditions etc

Our website can be found at www.harbourlaneictsupport.co.uk - here you'll get a feel for our branding. I've also attached 2 example documents - as well as our currently used documents. Hopefully you guys can see why it needs improving.

We'd also like to work with someone long term, these documents are a start but we'd like to make sure all the work we do looks and feels as smart as possible, so there is plenty of additional work available.

None of these templates need to be Print ready, 99% of the time it will be viewed digitally, so high resolution designs are best

Thanks,

Ned

Target Market(s)

Corporate & Educational Customers

Industry/Entity Type

It Support

Font styles to use
Sans Serif

Colors
ec1f27
0692cd
ffffff

```html
<!DOCTYPE html>
<html lang="en">
<head>
<meta charset="utf-8">
<title>Harbourlane ICT Support – Generic Document Template</title>
<link rel="stylesheet" href="https://fonts.googleapis.com/css2?family=Carlito:ital,wght@0,400;0,700;1,400&display=swap">
<style>
  :root {
    --brand-red: #d8121b;
    --brand-teal: #127a92;
    --heading-dark: #2f2f2f;
    --body-grey: #6b6b6b;
    --small-grey: #3d3d3d;
    --rule-grey: #9a9a9a;
    --paper: #ffffff;
  }
  * { margin: 0; padding: 0; box-sizing: border-box; }
  html, body { width: 851px; height: 1200px; overflow: hidden; background: var(--paper); }
  body { font-family: "Carlito", "Calibri", sans-serif; }

  .page { position: relative; width: 851px; height: 1200px; background: var(--paper); }

  .brand {
    position: absolute; top: 30px; right: 28px;
    font-weight: 700; font-size: 26px; line-height: 1; color: var(--brand-teal);
    white-space: nowrap;
  }

  .content { position: absolute; left: 56px; }
  .h1, .h2, .h3, .h4, .h5, .subsection { position: absolute; left: 56px; font-weight: 700; white-space: nowrap; }
  .h1 { top: 151px; font-size: 47px; color: var(--brand-teal); }
  .h2 { top: 243px; font-size: 39px; color: var(--brand-teal); }
  .h3 { top: 336px; font-size: 33px; color: var(--heading-dark); }
  .h4 { top: 426px; font-size: 28px; color: var(--heading-dark); }
  .h5 { top: 514px; font-size: 25px; color: var(--heading-dark); }
  .subsection { top: 573px; font-size: 23px; color: var(--brand-red); }

  .body-text {
    top: 617px; width: 735px;
    font-size: 26px; line-height: 35.5px; color: var(--body-grey);
  }
  .callout {
    top: 797px; width: 745px;
    font-size: 26px; line-height: 34px; font-style: italic; color: var(--brand-red);
  }
  .small-print {
    top: 930px; width: 770px;
    font-size: 19px; line-height: 29.7px; color: var(--small-grey);
  }

  .page-footer {
    position: absolute; right: 40px; top: 1140px;
    display: flex; align-items: center; gap: 10px;
    font-size: 19px; color: var(--small-grey);
  }
  .page-footer .divider { width: 1px; height: 36px; background: var(--rule-grey); }
  .page-footer .page-number { font-size: 21px; color: var(--heading-dark); }
</style>
</head>
<body>
<main class="page">
  <header class="brand">Harbourlane ICT Support</header>

  <h1 class="h1">H1 Heading Here</h1>
  <h2 class="h2">H2 Heading Here</h2>
  <h3 class="h3">H3 Heading Here</h3>
  <h4 class="h4">H4 Heading Here</h4>
  <h5 class="h5">H5 Heading Here</h5>
  <h6 class="subsection">Subsection Heading Text</h6>

  <p class="content body-text">Lorem Ipsum is simply dummy text of the printing and typesetting industry. Lorem Ipsum has been the industry's industry. Lorem Ipsum has been the finishLorem Ipsum is simply dummy text of the printing and typesetting industry.</p>

  <p class="content callout">Lorem Ipsum has been the industry's industry. Lorem Ipsum has been the finishLorem Ipsum is simply dummy text of the printing and typesetting industry.</p>

  <p class="content small-print">Lorem Ipsum is simply dummy text of the printing and typesetting industry. Lorem Ipsum has been the industry's industry. Lorem Ipsum has been the finishLorem Ipsum is simply dummy text of the printing and typesetting industry. Lorem Ipsum is simply dummy text of the printing and typesetting industry. Lorem Ipsum has been the industry's industry. Lorem Ipsum has been the finishLorem Ipsum is simply dummy text of the printing and typesetting industry.</p>

  <footer class="page-footer">
    <span class="classification">Confendtial</span>
    <span class="divider" aria-hidden="true"></span>
    <span class="page-number">1</span>
  </footer>
</main>
</body>
</html>
```